Website for Apartment Rental in Prague

I would like to create designs of my website focused on luxury apartment rentals in Prague, Czech Republic. I created initial mock-ups, They are all attached. I need to design homepage and subpage. The mock-ups were created by combining elements from different websites that I liked but I need you to create a design that is unique and original. The attached files a only a guidance for the structure of the website but not for the design. Try to be creative.

Apartment

```html
<!DOCTYPE html>
<html lang="en">
<head>
<meta charset="utf-8">
<title>La Mira Apartments</title>
<link rel="stylesheet" href="https://fonts.googleapis.com/css2?family=Lora:ital,wght@0,400;0,700;1,400&family=Roboto:wght@400;500;700&display=swap">
<style>
:root{
  --brown:#a27e68;
  --brown-dark:#8f6b55;
  --brown-band:#a58571;
  --ink:#333;
  --muted:#666;
  --line:#e3e3e3;
  --dark:#2b2b2b;
  --gold:#e0b43a;
  --white:#fff;
}
*{box-sizing:border-box;margin:0;padding:0}
html,body{width:1200px;height:2769px;overflow:hidden}
body{position:relative;background:var(--white);font-family:'Roboto',Arial,sans-serif;color:var(--ink)}
.abs{position:absolute}
/* top bar */
.topbar{left:0;top:0;width:1200px;height:52px;background:var(--brown);color:var(--white);font-size:13px;font-weight:500}
.topbar .item{position:absolute;top:18px;display:flex;align-items:center;gap:8px}
.topbar .sep{position:absolute;top:15px;width:1px;height:20px;background:rgba(255,255,255,.6)}
/* header */
.brand{left:0;top:52px;width:1200px;height:92px;text-align:center}
.brand .name{font-family:'Lora',serif;font-size:40px;color:var(--brown);padding-top:8px;line-height:48px}
.brand .sub{font-family:'Roboto',sans-serif;font-size:11px;letter-spacing:2px;font-weight:700;color:#333}
.nav{left:85px;top:144px;width:1030px;height:56px;border-top:1px solid #eee;display:flex;justify-content:space-between;align-items:center;padding:0 40px;font-size:11.5px;font-weight:500;color:#333}
/* hero */
.hero{left:0;top:200px;width:1200px;height:576px;background:linear-gradient(180deg,#cfcac3 0%,#8d8780 40%,#5d5853 62%,#a39a8f 85%,#8a8077 100%)}
.hero-arrow{position:absolute;top:464px;width:52px;height:52px;border:2px solid #fff;border-radius:50%;background:rgba(0,0,0,.15)}
.booking{left:114px;top:591px;width:975px;height:147px;background:rgba(248,243,232,.82);border:2px solid rgba(255,255,255,.8)}
.field{position:absolute;top:42px;font-size:11.5px;color:#444}
.field .box{margin-top:8px;height:38px;background:#fff;border:1px solid #ddd;position:relative}
.field .box svg{position:absolute;right:8px;top:13px}
.btn-avail{position:absolute;left:757px;top:20px;width:187px;height:42px;background:var(--brown);color:#fff;font-size:13px;font-weight:700;display:flex;align-items:center;justify-content:center}
.or{position:absolute;left:757px;top:66px;width:187px;text-align:center;font-family:'Lora',serif;font-style:italic;font-size:13px;color:#555}
.btn-unit{position:absolute;left:757px;top:88px;width:187px;height:42px;background:#3b3b3b;color:#fff;font-size:13px;font-weight:700;display:flex;align-items:center;justify-content:center}
/* welcome */
.welcome{left:150px;top:820px;width:900px;text-align:center}
.welcome h1{font-family:'Lora',serif;font-weight:400;font-size:33px;color:#333}
.welcome .lead{font-family:'Lora',serif;font-style:italic;color:var(--brown);font-size:15px;margin-top:14px}
.welcome p.body{font-size:11.5px;line-height:27px;color:#555;margin-top:12px}
.more{left:480px;top:1026px;width:240px;height:45px;border-radius:23px;background:var(--brown);color:#fff;font-family:'Lora',serif;font-style:italic;font-size:15px;display:flex;align-items:center;justify-content:center}
/* cards */
.card{position:absolute;width:332px;height:495px;border:1px solid var(--line);background:#fff}
.card .photo{height:218px}
.meta{height:48px;border-bottom:1px solid var(--line);display:flex;align-items:center;padding-left:14px;gap:10px;font-family:'Lora',serif;font-size:12px;color:#444}
.meta .bar{width:1px;height:16px;background:#bbb}
.meta span{display:flex;align-items:center;gap:6px}
.card h3{font-family:'Lora',serif;font-style:italic;font-weight:400;color:var(--brown);font-size:16px;line-height:26px;text-align:center;padding:18px 24px 0;height:78px}
.card p{font-size:11.5px;line-height:23px;color:#555;text-align:center;padding:0 20px}
.card .rule{position:absolute;left:30px;right:30px;top:415px;border-top:1px solid var(--line)}
.card .actions{position:absolute;left:42px;top:434px;display:flex;gap:8px}
.btn-view{width:120px;height:41px;background:var(--brown);color:#fff;font-size:12.5px;display:flex;align-items:center;justify-content:center}
.btn-book{width:122px;height:41px;border:1px solid var(--brown);color:var(--brown);font-size:12.5px;display:flex;align-items:center;justify-content:center}
.know{left:781px;top:1641px;width:332px;height:384px;border:1px solid var(--line);padding:22px 14px}
.know h2{font-family:'Lora',serif;font-weight:400;font-size:25px;color:#333}
.know h4{font-family:'Lora',serif;font-weight:400;font-size:13px;color:var(--brown);margin-top:28px;letter-spacing:.5px}
.know p{font-size:11.5px;line-height:22px;color:#444;margin-top:8px}
/* testimonial */
.testimonial{left:0;top:2206px;width:1200px;height:327px;background:linear-gradient(90deg,#a07d68,#b09381 50%,#a28370)}
.quote{position:absolute;left:176px;top:96px;width:540px;color:#fff;font-size:11.5px;line-height:23px}
.qmark{position:absolute;font-family:'Lora',serif;font-size:30px;color:#fff}
.who{position:absolute;left:176px;top:214px;color:#fff;font-weight:700;font-size:14px}
.when{position:absolute;left:176px;top:238px;color:#fff;font-size:12px}
.avatar{position:absolute;left:773px;top:68px;width:198px;height:198px;border-radius:50%;border:5px solid #fff;background:linear-gradient(160deg,#c49a7e,#7a5a44)}
/* footer */
.footer{left:0;top:2533px;width:1200px;height:236px;background:var(--dark);color:#ddd}
.social{position:absolute;top:34px;left:389px;display:flex;gap:13px}
.social .c{width:59px;height:59px;border:2px solid #cfcfcf;border-radius:50%;display:flex;align-items:center;justify-content:center}
.fnav{position:absolute;top:125px;left:85px;width:1030px;border-top:1px solid #444;padding-top:22px;display:flex;justify-content:center;gap:20px;font-size:11.5px;color:#ddd;font-family:'Lora',serif}
.fnav .s{color:#777}
.copy{position:absolute;top:178px;width:1200px;text-align:center;font-size:11.5px;color:#ccc;font-family:'Lora',serif}
</style>
</head>
<body>

<div class="abs topbar">
  <div class="item" style="left:86px"><svg width="14" height="14" viewBox="0 0 14 14"><path d="M2 1v13M2 2h9l-2 3 2 3H2" fill="none" stroke="#fff" stroke-width="1.4"/></svg>Discover Prague</div>
  <div class="sep" style="left:223px"></div>
  <div class="item" style="left:238px">Our Hospitality</div>
  <div class="item" style="left:587px"><svg width="14" height="11" viewBox="0 0 14 11"><rect x=".7" y=".7" width="12.6" height="9.6" fill="none" stroke="#fff" stroke-width="1.3"/><path d="M1 1l6 5 6-5" fill="none" stroke="#fff" stroke-width="1.3"/></svg>Email : reservation@miraprague-stays.com</div>
  <div class="sep" style="left:853px"></div>
  <div class="item" style="left:875px"><svg width="12" height="12" viewBox="0 0 12 12"><path d="M2 1l3 3-1.5 1.5a8 8 0 0 0 3 3L8 7l3 3-2 2C5 12 0 7 0 3z" fill="#fff"/></svg>Phone : 420 700 123 456</div>
  <div class="sep" style="left:1049px"></div>
  <div class="item" style="left:1069px">EN <svg width="8" height="5" viewBox="0 0 8 5"><path d="M0 0h8L4 5z" fill="#fff"/></svg></div>
</div>

<div class="abs brand">
  <div class="name">La Mira</div>
  <div class="sub">APARTMENTS</div>
</div>

<nav class="abs nav">
  <span>APARTMENT</span><span>LOCATION</span><span>SERVICES</span><span>GALLERY</span><span>NEWS</span><span>EXCLUSIVE OFFERS &amp;TOURS</span><span>FOR FAMILIES</span><span>CONTACT US</span>
</nav>

<div class="abs hero" role="img" aria-label="Modern luxury apartment living room with grey sofas and open kitchen"></div>
<div class="hero-arrow" style="left:24px"><svg width="48" height="48" viewBox="0 0 48 48"><path d="M28 15l-9 9 9 9" fill="none" stroke="#fff" stroke-width="3"/></svg></div>
<div class="hero-arrow" style="left:1122px"><svg width="48" height="48" viewBox="0 0 48 48"><path d="M20 15l9 9-9 9" fill="none" stroke="#fff" stroke-width="3"/></svg></div>

<div class="abs booking">
  <div class="field" style="left:16px;width:117px">Check in date<div class="box"><svg width="10" height="10" viewBox="0 0 10 10"><rect x=".5" y="1.5" width="9" height="8" fill="none" stroke="#999"/><path d="M.5 4h9" stroke="#999"/></svg></div></div>
  <div class="field" style="left:138px;width:117px">Check Out date<div class="box"><svg width="10" height="10" viewBox="0 0 10 10"><rect x=".5" y="1.5" width="9" height="8" fill="none" stroke="#999"/><path d="M.5 4h9" stroke="#999"/></svg></div></div>
  <div class="field" style="left:260px;width:82px">Adults<div class="box"><svg width="8" height="5" viewBox="0 0 8 5"><path d="M0 0h8L4 5z" fill="#999"/></svg></div></div>
  <div class="field" style="left:347px;width:82px">Children<div class="box"><svg width="8" height="5" viewBox="0 0 8 5"><path d="M0 0h8L4 5z" fill="#999"/></svg></div></div>
  <div class="field" style="left:434px;width:82px">Infants<div class="box"><svg width="8" height="5" viewBox="0 0 8 5"><path d="M0 0h8L4 5z" fill="#999"/></svg></div></div>
  <div class="field" style="left:521px;width:210px">Promotional Code<div class="box"></div></div>
  <div class="btn-avail">CHECK AVALIABILITY</div>
  <div class="or">OR</div>
  <div class="btn-unit">SELECT RENTAL UNIT</div>
</div>

<section class="abs welcome">
  <h1>Welcome to La Mira</h1>
  <div class="lead">Sed ut perspiciatis unde omnis iste natus error sit voluptatem accusantium doloremque laudantium</div>
  <p class="body">Sed ut perspiciatis unde omnis iste natus error sit voluptatem accusantium doloremque laudantium, totam rem aperiam, eaque ipsa quae ab illo<br>inventore veritatis et quasi architecto beatae vitae dicta sunt explicabo. Nemo enim ipsam voluptatem quia voluptas sit aspernatur aut odit aut fugit,<br>sed quia consequuntur magni dolores eos qui ratione voluptatem sequi nesciunt.</p>
</section>
<div class="abs more">Click Here For More Info</div>

<!-- apartment cards -->
<article class="card" style="left:85px;top:1122px">
  <div class="photo" role="img" aria-label="Bright living room with sea view windows" style="background:linear-gradient(180deg,#9fb6c6,#d9dcdc 60%,#bdb8ae)"></div>
  <div class="meta"><span><svg width="14" height="10" viewBox="0 0 14 10"><path d="M0 0v10M0 7h14v3M3 4h11v3" fill="none" stroke="#666" stroke-width="1.5"/></svg>1 Bedroom</span><i class="bar"></i><span><svg width="10" height="11" viewBox="0 0 10 11"><circle cx="5" cy="3" r="2.6" fill="#666"/><path d="M0 11a5 5 0 0 1 10 0z" fill="#666"/></svg>Max 4 People</span><i class="bar"></i><span><svg width="56" height="10" viewBox="0 0 56 10"><g fill="none" stroke="#e0b43a"><path id="st" d="M5 .8l1.2 2.8 3 .3-2.3 2 .7 3-2.6-1.6-2.6 1.6.7-3-2.3-2 3-.3z"/><use href="#st" x="11"/><use href="#st" x="22"/><use href="#st" x="33"/></g><path d="M49 .8l1.2 2.8 3 .3-2.3 2 .7 3-2.6-1.6-2.6 1.6.7-3-2.3-2 3-.3z" fill="#e0b43a"/></svg></span></div>
  <h3>Brand New Luxury Living Stunning Contemporary Design</h3>
  <p>Sed ut perspiciatis unde omnis iste natus error sit volu accusantium doloremque laudantium explicabo.</p>
  <div class="rule"></div>
  <div class="actions"><div class="btn-view">VIEW DETAILS</div><div class="btn-book">BOOK NOW</div></div>
</article>

<article class="card" style="left:434px;top:1122px">
  <div class="photo" role="img" aria-label="White kitchen with marble island and pendant lights" style="background:linear-gradient(180deg,#6c6560,#cfc8c0 55%,#e8e3dc)"></div>
  <div class="meta"><span><svg width="14" height="10" viewBox="0 0 14 10"><path d="M0 0v10M0 7h14v3M3 4h11v3" fill="none" stroke="#666" stroke-width="1.5"/></svg>1 Bedroom</span><i class="bar"></i><span><svg width="10" height="11" viewBox="0 0 10 11"><circle cx="5" cy="3" r="2.6" fill="#666"/><path d="M0 11a5 5 0 0 1 10 0z" fill="#666"/></svg>Max 4 People</span><i class="bar"></i><span><svg width="56" height="10" viewBox="0 0 56 10"><g fill="none" stroke="#e0b43a"><use href="#st"/><use href="#st" x="11"/><use href="#st" x="22"/><use href="#st" x="33"/></g><use href="#st" x="44" fill="#e0b43a"/></svg></span></div>
  <h3>Brand New Zen Luxury Living Apart-ment in the Center of Prague</h3>
  <p>Sed ut perspiciatis unde omnis iste natus error sit volu accusantium doloremque laudantium explicabo.</p>
  <div class="rule"></div>
  <div class="actions"><div class="btn-view">VIEW DETAILS</div><div class="btn-book">BOOK NOW</div></div>
</article>

<article class="card" style="left:781px;top:1122px">
  <div class="photo" role="img" aria-label="Minimal lounge with glossy black floor and garden view" style="background:linear-gradient(180deg,#e5e5e2,#c9c8c3 55%,#3a3634)"></div>
  <div class="meta"><span><svg width="14" height="10" viewBox="0 0 14 10"><path d="M0 0v10M0 7h14v3M3 4h11v3" fill="none" stroke="#666" stroke-width="1.5"/></svg>1 Bedroom</span><i class="bar"></i><span><svg width="10" height="11" viewBox="0 0 10 11"><circle cx="5" cy="3" r="2.6" fill="#666"/><path d="M0 11a5 5 0 0 1 10 0z" fill="#666"/></svg>Max 4 People</span><i class="bar"></i><span><svg width="56" height="10" viewBox="0 0 56 10"><g fill="none" stroke="#e0b43a"><use href="#st"/><use href="#st" x="11"/><use href="#st" x="22"/><use href="#st" x="33"/></g><use href="#st" x="44" fill="#e0b43a"/></svg></span></div>
  <h3>Expedition Prague Top Loca Brand New Apartment</h3>
  <p>Sed ut perspiciatis unde omnis iste natus error sit volu accusantium doloremque laudantium explicabo.</p>
  <div class="rule"></div>
  <div class="actions"><div class="btn-view">VIEW DETAILS</div><div class="btn-book">BOOK NOW</div></div>
</article>

<article class="card" style="left:85px;top:1641px">
  <div class="photo" role="img" aria-label="Sunny penthouse living room with wooden floor" style="background:linear-gradient(180deg,#8a6848,#c9ad8a 50%,#7e5a3c)"></div>
  <div class="meta"><span><svg width="14" height="10" viewBox="0 0 14 10"><path d="M0 0v10M0 7h14v3M3 4h11v3" fill="none" stroke="#666" stroke-width="1.5"/></svg>1 Bedroom</span><i class="bar"></i><span><svg width="10" height="11" viewBox="0 0 10 11"><circle cx="5" cy="3" r="2.6" fill="#666"/><path d="M0 11a5 5 0 0 1 10 0z" fill="#666"/></svg>Max 4 People</span><i class="bar"></i><span><svg width="56" height="10" viewBox="0 0 56 10"><g fill="none" stroke="#e0b43a"><use href="#st"/><use href="#st" x="11"/><use href="#st" x="22"/><use href="#st" x="33"/></g><use href="#st" x="44" fill="#e0b43a"/></svg></span></div>
  <h3>Brand New Sunny Penthouse Eith A View of Prague</h3>
  <p>Sed ut perspiciatis unde omnis iste natus error sit volu accusantium doloremque laudantium explicabo.</p>
  <div class="rule"></div>
  <div class="actions"><div class="btn-view">VIEW DETAILS</div><div class="btn-book">BOOK NOW</div></div>
</article>

<article class="card" style="left:434px;top:1641px">
  <div class="photo" role="img" aria-label="Entrance hall with curved staircase" style="background:linear-gradient(180deg,#5a4030,#a88c6e 50%,#3b2a20)"></div>
  <div class="meta"><span><svg width="14" height="10" viewBox="0 0 14 10"><path d="M0 0v10M0 7h14v3M3 4h11v3" fill="none" stroke="#666" stroke-width="1.5"/></svg>1 Bedroom</span><i class="bar"></i><span><svg width="10" height="11" viewBox="0 0 10 11"><circle cx="5" cy="3" r="2.6" fill="#666"/><path d="M0 11a5 5 0 0 1 10 0z" fill="#666"/></svg>Max 4 People</span><i class="bar"></i><span><svg width="56" height="10" viewBox="0 0 56 10"><g fill="none" stroke="#e0b43a"><use href="#st"/><use href="#st" x="11"/><use href="#st" x="22"/><use href="#st" x="33"/></g><use href="#st" x="44" fill="#e0b43a"/></svg></span></div>
  <h3>Brand New Modern Apartment Unbeat-able Location</h3>
  <p>Sed ut perspiciatis unde omnis iste natus error sit volu accusantium doloremque laudantium explicabo.</p>
  <div class="rule"></div>
  <div class="actions"><div class="btn-view">VIEW DETAILS</div><div class="btn-book">BOOK NOW</div></div>
</article>

<aside class="abs know">
  <h2>Need To Know</h2>
  <h4>APARTMENTS</h4>
  <p>also available to rent all the apartment Together for<br>companies or Larger Groups</p>
  <h4>CHECK - OUT</h4>
  <p>12 noon ealkiest check - in,3pm-both are flexible<br>by arrangement</p>
  <h4>RATES</h4>
  <p>Prices from 150 USD per noght Including tax</p>
</aside>

<section class="abs testimonial">
  <svg class="abs" style="left:48px;top:100px" width="20" height="90" viewBox="0 0 20 90"><path d="M18 0L2 45l16 45" fill="none" stroke="rgba(255,255,255,.5)" stroke-width="1.5"/></svg>
  <svg class="abs" style="left:1132px;top:100px" width="20" height="90" viewBox="0 0 20 90"><path d="M2 0l16 45L2 90" fill="none" stroke="rgba(255,255,255,.5)" stroke-width="1.5"/></svg>
  <div class="qmark" style="left:158px;top:72px">&ldquo;</div>
  <p class="quote">Sed ut perspiciatis unde omnis iste natus error sit voluptatem accusantium doloremque laudantium, totam rem aperiam, eaque ipsa quae ab illo inventore veritatis et quasi architecto beatae vitae dicta sunt explicabo. Nemo enim ipsam voluptatem quia voluptas sit aspernatur aut odit aut fugit, sed quia consequuntur magni dolores eos qui ratione voluptatem sequi nesciunt.</p>
  <div class="qmark" style="left:558px;top:180px">&rdquo;</div>
  <div class="who">ANNA NOVAK</div>
  <div class="when">Posted On 07 Nov 2017</div>
  <div class="avatar" role="img" aria-label="Guest portrait"></div>
</section>

<footer class="abs footer">
  <div class="social">
    <div class="c" aria-label="Social network 1"></div>
    <div class="c" aria-label="Social network 2"></div>
    <div class="c" aria-label="Social network 3"></div>
    <div class="c" aria-label="Social network 4"></div>
    <div class="c" aria-label="Social network 5"></div>
    <div class="c" aria-label="Email"><svg width="18" height="13" viewBox="0 0 18 13"><rect x=".8" y=".8" width="16.4" height="11.4" rx="1.5" fill="none" stroke="#ddd" stroke-width="1.5"/><path d="M1 1.5l8 6 8-6" fill="none" stroke="#ddd" stroke-width="1.5"/></svg></div>
  </div>
  <div class="fnav"><span>APARTMENT</span><span class="s">|</span><span>LOCATION</span><span class="s">|</span><span>SERVICES</span><span class="s">|</span><span>GALLERY</span><span class="s">|</span><span>NEWS</span><span class="s">|</span><span>EXCLUSIVE OFFERS &amp; TOURS</span><span class="s">|</span><span>FOR FAMILIES</span><span class="s">|</span><span>CONTACT US</span></div>
  <div class="copy">© Copyrights 2017 La Mira.All&nbsp; Rights Reserved.</div>
</footer>

</body>
</html>
```